Private Investigation Business Card Design

I need a business card for a new private investigation company named Brisk Inquiries. I perform mainly surveillance jobs, vehicle repossessions, document serves etc. The final design should aim for a professional look. The logo has a magnifying glass with stick man arms and legs and is in a running action to show the "Brisk" aspect of the name. If the colour scheme could remain the same as the website www.briskinquiries-demo.com.au with silvers,blacks and a couple electric blue highlights.
Industry/Entity Type
Business
Contact Information for Business Card
Morgan Kellaway
Brisk Inquiries
0487316204
PO Box 58, Carnwell NSW 2291
info@briskinquiries-demo.com.au
www.briskinquiries-demo.com.au
Look and feel

```html
<!DOCTYPE html>
<html lang="en">
<head>
<meta charset="utf-8">
<title>Brisk Inquiries – Business Card</title>
<link rel="stylesheet" href="https://fonts.googleapis.com/css2?family=Arimo:wght@400;700&display=swap">
<style>
  :root {
    --backdrop: #1f1f21;
    --card-white: #ffffff;
    --card-silver: #d9d9dc;
    --panel-dark: #8e8c92;
    --panel-light: #bdbbc0;
    --ink: #1a1a1a;
    --ink-soft: #3a3a3d;
    --divider: #111111;
  }
  * { box-sizing: border-box; margin: 0; padding: 0; }
  html, body {
    width: 1200px; height: 871px; overflow: hidden;
    background: var(--backdrop);
    font-family: "Arimo", Arial, sans-serif;
  }
  .sheet {
    width: 1200px; height: 871px;
    display: flex; flex-direction: column; align-items: center; justify-content: center;
    gap: 40px;
  }
  .card {
    width: 560px; height: 342px;
    border-radius: 3px;
    overflow: hidden;
    position: relative;
  }
  /* Back side */
  .card-back {
    background: linear-gradient(135deg, var(--card-white) 0%, var(--card-silver) 100%);
    display: flex; flex-direction: column; align-items: center; justify-content: center;
  }
  .brand-mark {
    display: flex; align-items: center; gap: 16px;
  }
  .brand-dot {
    width: 22px; height: 22px; border-radius: 50%;
    background: var(--ink);
  }
  .brand-name {
    font-size: 40px; font-weight: 700; color: var(--ink);
    letter-spacing: 1px;
  }
  .back-url {
    position: absolute; bottom: 34px; left: 0; right: 0;
    text-align: center;
    font-size: 13px; letter-spacing: 3px; color: var(--ink-soft);
  }
  /* Front side */
  .card-front { display: flex; }
  .contact-panel {
    width: 50%; height: 100%;
    background: radial-gradient(ellipse at 60% 40%, var(--panel-light) 0%, var(--panel-dark) 100%);
    padding: 44px 30px 0 34px;
    border-right: 3px solid var(--divider);
  }
  .contact-name {
    font-size: 20px; font-weight: 700; color: var(--ink);
    margin-bottom: 26px;
  }
  .contact-address {
    font-size: 13px; color: var(--ink-soft); line-height: 1.35;
    margin-bottom: 8px;
  }
  .contact-list { list-style: none; }
  .contact-list li {
    display: flex; align-items: center; gap: 10px;
    font-size: 13px; color: var(--ink-soft);
    margin-bottom: 6px;
  }
  .contact-list svg { width: 13px; height: 13px; flex: none; fill: var(--ink); }
  .logo-panel {
    width: 50%; height: 100%;
    background: linear-gradient(135deg, var(--card-white) 0%, var(--card-silver) 100%);
    display: flex; align-items: center; justify-content: center;
  }
  .logo-panel .brand-name { font-size: 30px; }
  .logo-panel .brand-dot { width: 16px; height: 16px; }
</style>
</head>
<body>
<main class="sheet">
  <section class="card card-back" aria-label="Card back">
    <div class="brand-mark">
      <span class="brand-name">Brisk Inquiries</span>
      <span class="brand-dot"></span>
    </div>
    <p class="back-url">www.briskinquiries-demo.com.au</p>
  </section>

  <section class="card card-front" aria-label="Card front">
    <div class="contact-panel">
      <h1 class="contact-name">Morgan Kellaway</h1>
      <p class="contact-address">PO Box 58<br>Carnwell NSW 2291</p>
      <ul class="contact-list">
        <li>
          <svg viewBox="0 0 16 16" aria-hidden="true"><path d="M3 1h3l1.5 4-2 1.3a9 9 0 0 0 4.2 4.2L11 8.5l4 1.5v3a2 2 0 0 1-2 2A12 12 0 0 1 1 3a2 2 0 0 1 2-2z"/></svg>
          0487 316 204
        </li>
        <li>
          <svg viewBox="0 0 16 16" aria-hidden="true"><path d="M1 3h14v10H1z M1 3l7 6 7-6" fill="none" stroke="#1a1a1a" stroke-width="1.6"/></svg>
          info@briskinquiries-demo.com.au
        </li>
        <li>
          <svg viewBox="0 0 16 16" aria-hidden="true"><circle cx="8" cy="8" r="7"/></svg>
          www.briskinquiries-demo.com.au
        </li>
      </ul>
    </div>
    <div class="logo-panel">
      <div class="brand-mark">
        <span class="brand-name">Brisk Inquiries</span>
        <span class="brand-dot"></span>
      </div>
    </div>
  </section>
</main>
</body>
</html>
```